Vale Linebacker Needs a new website!

We need a four page website for a new company based in San Francisco. We help companies connect better with their clients, employees, and vendors by implementing collaborative technology.
Similar Websites
Mist Rangers - http://www.mistrangers.example/
Skyforthing - http://www.skyforthing.example/ - I don't like the the rotating window or the pictures of people. I like the icons used to go to the next pages.
Color Combos
Blues and Yellows - http://www.huepairings.example/palette-sets/96/HuePairing96.html
We prefer graphics over the actual pictures of people in the header. Pictures of people working together in the text is fine.
Web Page Layout
Index
Cloud Advisory Services
Email Everywhere
CRM Implementation
For detailed copy please see this link https://files.paperhold.example/a/widgetladyla.example/document/d/7KtmPzWqAeRbYcNvHsJgLdFxTuQoIeMnBvCxZaSdFgHj/edit
Industry/Entity Type
It Company

```html
<!DOCTYPE html>
<html lang="en">
<head>
<meta charset="utf-8">
<title>Vale Linebacker</title>
<link href="https://fonts.googleapis.com/css2?family=Open+Sans:wght@400;600;700&family=PT+Sans:wght@700&display=swap" rel="stylesheet">
<style>
:root{
  --blue:#2466b5;
  --blue-dark:#1d579c;
  --yellow:#fbb800;
  --ink:#2b2b2b;
  --text:#444;
  --muted:#777;
  --light:#f2f2f2;
  --line:#cfcfcf;
  --black:#1c1c1c;
  --white:#fff;
}
*{box-sizing:border-box;margin:0;padding:0}
html,body{width:1200px;height:2244px;overflow:hidden}
body{position:relative;background:var(--white);font-family:"Open Sans",Arial,sans-serif;color:var(--text)}
.abs{position:absolute}
ul{list-style:none}

/* header */
.site-header{position:absolute;left:0;top:0;width:1200px;height:104px;background:var(--white)}
.brand{position:absolute;left:192px;top:30px;display:flex;align-items:center;gap:10px}
.brand-dot{width:34px;height:34px;border-radius:50%;background:var(--blue)}
.brand-name{font-weight:700;font-size:22px;color:var(--blue)}
.main-nav{position:absolute;left:563px;top:45px;display:flex;gap:26px;font-size:12.5px;color:var(--ink)}
.main-nav a{color:inherit;text-decoration:none}
.main-nav .current{font-weight:600}

/* hero */
.hero{position:absolute;left:0;top:104px;width:1200px;height:436px;background:linear-gradient(100deg,#6d7f95 0%,#b9c6d4 35%,#e4e9ef 60%,#f4f6f8 100%)}
.hero-caption{position:absolute;left:580px;top:74px;width:545px;height:96px;background:rgba(90,90,90,.85);color:var(--white);text-align:center;padding-top:14px}
.hero-caption h1{font-family:"PT Sans",Arial,sans-serif;font-size:29px;font-weight:700}
.hero-caption p{font-family:"PT Sans",Arial,sans-serif;font-size:14.5px;font-weight:700;margin-top:4px}
.hero-dots{position:absolute;left:1114px;top:402px;display:flex;gap:5px}
.hero-dots span{width:7px;height:7px;border-radius:50%;background:var(--white)}
.hero-dots .on{background:var(--blue)}

/* services */
.service{position:absolute;top:564px;width:246px;text-align:center}
.service-icon{width:66px;height:66px;border-radius:50%;background:var(--yellow);margin:0 auto;display:flex;align-items:center;justify-content:center}
.service h2{font-size:16px;font-weight:600;color:var(--ink);margin-top:24px}
.service p{font-size:10.5px;line-height:18px;color:var(--ink);text-align:justify;text-align-last:center;margin-top:12px}
.more{font-size:10px;color:var(--ink);text-transform:uppercase;display:flex;align-items:center;gap:8px}
.service .more{justify-content:center;margin-top:22px}

/* blog + video band */
.media-band{position:absolute;left:0;top:830px;width:1200px;height:335px;background:var(--blue);color:var(--white)}
.band-title{position:absolute;top:32px;font-size:16px;font-weight:600;text-transform:uppercase}
.blog-item{position:absolute;left:198px;width:275px;height:75px;display:flex;align-items:center;gap:14px;border-bottom:1px solid rgba(255,255,255,.25)}
.blog-item:last-child{border-bottom:0}
.blog-thumb{flex:none;width:54px;height:54px;border-radius:50%;border:3px solid var(--white);background:linear-gradient(135deg,#d9e1ea,#7e93ad)}
.blog-item p{font-size:10px;font-weight:600;line-height:18px}
.video{position:absolute;left:578px;top:86px;width:354px;height:214px;background:linear-gradient(135deg,#e9edf1,#a9b9cb 55%,#6f86a3)}
.video-bar{position:absolute;left:0;bottom:0;width:100%;height:36px;background:#3a3a3a;display:flex;align-items:center;padding:0 10px;gap:14px}
.video-track{flex:1;height:5px;background:#777;position:relative}
.video-track span{position:absolute;left:0;top:0;height:5px;width:60%;background:var(--white)}

/* what we do */
.about-photo{position:absolute;left:191px;top:1221px;width:365px;height:190px;border:1px solid var(--line);background:linear-gradient(120deg,#e6ebf0,#b6c3d2 50%,#5d6f85)}
.about-copy{position:absolute;left:582px;top:1218px;width:388px}
.about-copy h2{font-size:17px;font-weight:600;color:var(--ink);padding-bottom:10px;border-bottom:1px solid var(--line)}
.about-copy p{font-size:10.5px;line-height:18px;color:var(--ink);margin-top:18px}
.about-copy li{font-size:10.5px;line-height:18px;color:var(--ink);display:flex;align-items:center;gap:10px}
.about-copy li::before{content:"";width:6px;height:6px;background:var(--blue)}
.about-copy .more{margin-top:12px}

/* clients */
.clients{position:absolute;left:0;top:1465px;width:1200px;height:184px;background:var(--light)}
.section-title{font-size:16px;font-weight:600;color:var(--ink);text-transform:uppercase;text-align:center;letter-spacing:-.2px}
.clients .section-title{position:absolute;left:0;top:30px;width:100%}
.client-row{position:absolute;left:198px;top:88px;display:flex;gap:11px}
.client{width:103px;height:57px;border:1px solid #c9c9c9;background:var(--light);display:flex;align-items:center;justify-content:center;font-size:13px;font-weight:700;color:#555}

/* testimonials */
.testimonials .section-title{position:absolute;left:0;top:1700px;width:100%}
.testi-photo{position:absolute;left:237px;top:1757px;width:90px;height:75px;border:1px solid var(--line);background:linear-gradient(135deg,#eef2f6,#9fb2c7)}
.testi-text{position:absolute;left:345px;top:1755px;width:607px;font-size:10.5px;line-height:19.5px;color:var(--text);text-align:justify}
.testi-name{position:absolute;left:343px;top:1850px;font-size:11px;color:var(--muted)}
.testi-name b{color:#333}
.arrow{position:absolute;top:1788px;width:16px;height:16px;border-radius:50%;background:#e2e2e2;display:flex;align-items:center;justify-content:center}

/* footer */
.site-footer{position:absolute;left:0;top:1913px;width:1200px;height:259px;background:var(--blue);color:var(--white)}
.foot-col{position:absolute;top:40px}
.foot-col h3{font-size:15px;font-weight:400;text-transform:uppercase}
.foot-col p{font-size:10px;line-height:16px;margin-top:30px}
.contact-line{display:flex;align-items:center;gap:14px;font-size:10px;margin-top:10px}
.contact-line svg{flex:none}
.tweet{display:flex;gap:10px;font-size:10px;line-height:16px;margin-top:22px}
.tweet-mark{flex:none;width:10px;height:10px;border-radius:50%;background:var(--white);margin-top:3px}
.tweet small{display:block;font-size:10px;margin-top:6px}
.newsletter{display:flex;margin-top:22px}
.newsletter span{width:126px;height:28px;background:var(--white);color:#aaa;font-size:10px;padding:8px 12px}
.newsletter b{width:34px;height:28px;background:var(--blue-dark);font-size:10px;font-weight:400;display:flex;align-items:center;justify-content:center;border:1px solid rgba(255,255,255,.3)}

/* bottom bar */
.bottom-bar{position:absolute;left:0;top:2172px;width:1200px;height:72px;background:var(--black);color:var(--white)}
.bottom-bar p{position:absolute;left:190px;top:28px;font-size:10.5px}
.social{position:absolute;left:928px;top:25px;display:flex;gap:6px}
.social span{width:23px;height:23px;border-radius:50%;background:var(--white)}
</style>
</head>
<body>

<header class="site-header">
  <div class="brand"><span class="brand-dot"></span><span class="brand-name">Vale Linebacker</span></div>
  <nav class="main-nav">
    <a class="current">Home</a>
    <a>Cloud Advisory Services</a>
    <a>Email Everywhere</a>
    <a>CRM Implementation</a>
  </nav>
</header>

<section class="hero" role="img" aria-label="Photo of two colleagues looking at a phone beside a laptop in a bright office">
  <div class="hero-caption">
    <h1>Suspendisse mauris. Fusce accumsan mollis</h1>
    <p>Pellentesque a diam sit amet mi ullamcorper vehicula. Integer adipiscing</p>
  </div>
  <div class="hero-dots"><span class="on"></span><span></span><span></span><span></span></div>
</section>

<section class="services">
  <article class="service" style="left:193px">
    <div class="service-icon"><svg width="30" height="30" viewBox="0 0 30 30"><circle cx="15" cy="10" r="6" fill="none" stroke="#fff" stroke-width="2.4"/><path d="M4 26c1-6 6-9 11-9s10 3 11 9z" fill="none" stroke="#fff" stroke-width="2.4"/></svg></div>
    <h2>Cloud Advisory Services</h2>
    <p>Maecenas ipsum metus, semper hendrerit varius mattis, congue sit amet tellus. Aliquam ullamcorper dui sed magna posue re ut elementum enim rutrum. Nam mi erat, porta id ultrices nec.</p>
    <div class="more"><svg width="12" height="8" viewBox="0 0 12 8"><path d="M1 0l4 4-4 4M6 0l4 4-4 4" fill="none" stroke="#222" stroke-width="1.8"/></svg>Find out more</div>
  </article>
  <article class="service" style="left:469px;top:560px">
    <div class="service-icon"><svg width="28" height="22" viewBox="0 0 28 22"><rect x="1" y="1" width="26" height="20" rx="2" fill="#fff"/><path d="M2 3l12 9 12-9" fill="none" stroke="#fbb800" stroke-width="2"/></svg></div>
    <h2>Email Everywhere</h2>
    <p>Maecenas ipsum metus, semper hendrerit varius mattis, congue sit amet tellus. Aliquam ullamcorper dui sed magna posue re ut elementum enim rutrum. Nam mi erat, porta id ultrices nec</p>
    <div class="more"><svg width="12" height="8" viewBox="0 0 12 8"><path d="M1 0l4 4-4 4M6 0l4 4-4 4" fill="none" stroke="#222" stroke-width="1.8"/></svg>Find out more</div>
  </article>
  <article class="service" style="left:768px">
    <div class="service-icon"><svg width="30" height="30" viewBox="0 0 30 30"><path d="M15 2a12 12 0 1 0 7 22l5 3-2-6A12 12 0 0 0 15 2z" fill="#fff"/><text x="15" y="20" text-anchor="middle" font-family="Open Sans,sans-serif" font-weight="700" font-size="15" fill="#fbb800">?</text></svg></div>
    <h2>CRM Solutions</h2>
    <p>Maecenas ipsum metus, semper hendrerit varius mattis, congue sit amet tellus. Aliquam ullamcorper dui sed magna posue re ut elementum enim rutrum. Nam mi erat, porta id ultrices nec</p>
    <div class="more"><svg width="12" height="8" viewBox="0 0 12 8"><path d="M1 0l4 4-4 4M6 0l4 4-4 4" fill="none" stroke="#222" stroke-width="1.8"/></svg>Find out more</div>
  </article>
</section>

<section class="media-band">
  <h2 class="band-title" style="left:202px">Our Blog</h2>
  <div class="blog-list">
    <div class="blog-item" style="top:70px"><div class="blog-thumb" role="img" aria-label="Photo of a person at a desk"></div><p>In ultricies pellentesque massa a porta. Aliquam ipsum enim, hendrerit ut porta nec. ullamcorper et nulla. In eget mi dui, sit amet.</p></div>
    <div class="blog-item" style="top:146px"><div class="blog-thumb" role="img" aria-label="Photo of a team meeting"></div><p>In ultricies pellentesque massa a porta. Aliquam ipsum enim, hendrerit ut porta nec. ullamcorper et nulla. In eget mi dui, sit amet.</p></div>
    <div class="blog-item" style="top:222px;border-bottom:0"><div class="blog-thumb" role="img" aria-label="Photo of a colleague at work"></div><p>In ultricies pellentesque massa a porta. Aliquam ipsum enim, hendrerit ut porta nec. ullamcorper et nulla. In eget mi dui, sit amet.</p></div>
  </div>
  <h2 class="band-title" style="left:582px">Our Videos</h2>
  <div class="video" role="img" aria-label="Video still of three colleagues working together at a laptop">
    <div class="video-bar">
      <svg width="12" height="14" viewBox="0 0 12 14"><path d="M1 1l10 6-10 6z" fill="#fff"/></svg>
      <div class="video-track"><span></span></div>
      <svg width="16" height="14" viewBox="0 0 16 14"><path d="M1 5h3l4-4v12l-4-4H1z" fill="#fff"/><path d="M11 4c1.5 1.5 1.5 4.5 0 6M13 2c3 3 3 7 0 10" fill="none" stroke="#fff" stroke-width="1.3"/></svg>
    </div>
  </div>
</section>

<section class="about">
  <div class="about-photo" role="img" aria-label="Photo of a smiling business team in an office"></div>
  <div class="about-copy">
    <h2>WHAT WE DO</h2>
    <p>We challenge the status quo by providing unique insights, emerging strategies and proven best practices. Our unwavering focus is on customer satisfaction. Our services include:</p>
    <ul style="margin-top:2px">
      <li>Strategy</li><li>Migration</li><li>Implementation</li><li>Integration</li>
    </ul>
    <div class="more" style="margin-left:-4px"><svg width="12" height="8" viewBox="0 0 12 8"><path d="M1 0l4 4-4 4M6 0l4 4-4 4" fill="none" stroke="#222" stroke-width="1.8"/></svg>Find out more</div>
  </div>
</section>

<section class="clients">
  <h2 class="section-title">Our Clients</h2>
  <div class="client-row">
    <div class="client">Tessera</div>
    <div class="client">Brook &amp; Vane</div>
    <div class="client">Farelux</div>
    <div class="client">Graymont</div>
    <div class="client">Harlow</div>
    <div class="client">Genwick</div>
    <div class="client">Tradeloop</div>
  </div>
</section>

<section class="testimonials">
  <h2 class="section-title">Client Testimonials</h2>
  <div class="arrow" style="left:189px"><svg width="6" height="8" viewBox="0 0 6 8"><path d="M5 0L1 4l4 4" fill="none" stroke="#fff" stroke-width="1.5"/></svg></div>
  <div class="testi-photo" role="img" aria-label="Photo of a smiling client with colleagues"></div>
  <p class="testi-text">Lorem Ipsum is simply dummy text of the printing and typesetting industry. Lorem Ipsum has been the industry's standard dummy text ever since type specimen book Lorem Ipsum is simply dummy text of the printing and typesetting industry. Lorem Ipsum has been the industry's standard dummy text ever since type specimen book Lorem Ipsum is simply dummy text of the printing and typesetting industry. Lorem Ipsum has been ever since type specimen book !!</p>
  <p class="testi-name"><b>- Orin Pell</b>, Company Name</p>
  <div class="arrow" style="left:993px"><svg width="6" height="8" viewBox="0 0 6 8"><path d="M1 0l4 4-4 4" fill="none" stroke="#fff" stroke-width="1.5"/></svg></div>
</section>

<footer class="site-footer">
  <div class="foot-col" style="left:190px;width:170px">
    <h3>About Us</h3>
    <p>Ray Dunmore and Tess Okafor have combined their expertise and international team to offer quality advice on cloud strategies. Our objective is to provide guidance, thought leadership and strategic support to make the right decisions as you move your company forward.</p>
  </div>
  <div class="foot-col" style="left:406px;width:160px">
    <h3>Contact</h3>
    <p style="margin-bottom:6px">There are many variations of passages of Lorem Ipsum available, but the majority have suffered alteration in so</p>
    <div class="contact-line"><svg width="12" height="15" viewBox="0 0 12 15"><path d="M6 0a6 6 0 0 0-6 6c0 4 6 9 6 9s6-5 6-9a6 6 0 0 0-6-6z" fill="#fff"/><circle cx="6" cy="6" r="2.2" fill="#2466b5"/></svg>Adress</div>
    <div class="contact-line"><svg width="14" height="11" viewBox="0 0 14 11"><rect width="14" height="11" rx="1" fill="#fff"/><path d="M1 1l6 5 6-5" fill="none" stroke="#2466b5" stroke-width="1.3"/></svg>info@valelinebacker.example</div>
    <div class="contact-line"><svg width="13" height="13" viewBox="0 0 13 13"><path d="M3 0l2 3-1.5 1.5c.8 2 2.5 3.7 4.5 4.5L9.5 7.5l3 2L11 12.5C5 12 1 8 .5 2z" fill="#fff"/></svg>555-01420-67890</div>
  </div>
  <div class="foot-col" style="left:613px;width:190px">
    <h3>Latest Tweets</h3>
    <div class="tweet"><span class="tweet-mark"></span><div>Lorem Ipsum is simply dummy text of the printing and typesetting industry. Lorem Ipsum has been the industry's standard dummy<small>1 Hour Ago</small></div></div>
    <div class="tweet" style="margin-top:12px"><span class="tweet-mark"></span><div>Lorem Ipsum is simply dummy text of the printing and typesetting<small>1 Hour Ago</small></div></div>
  </div>
  <div class="foot-col" style="left:848px;width:170px">
    <h3>News Letter</h3>
    <p>Type your email address below and recive our daily news letter for free</p>
    <div class="newsletter"><span>Email Address</span><b>GO</b></div>
  </div>
</footer>

<div class="bottom-bar">
  <p>© Copy right 2014 Vale Linebacker | All rights reserved.</p>
  <div class="social"><span></span><span></span><span></span></div>
</div>

</body>
</html>
```